Tallowmere Exteriors Door Hanger design, Postcard and presentation folders Design

we are a home improvement company in Portland Oregon, are main service is roofing but we also do gutters, painting and pressure washing. we are a certified roofing contractor for KRV. We have over 20years of experince in the roofing industry we use top quality materials. Our mission is to do quality work and provide the best service.
Updates

This door hangers are going to be share to homeowners where we are currently working at! I will like to have a square maybe 2 inch wide and 1 inch hide (blank) for me to put the address where we are working at. So we want to give a direct message to homeowners who we are and why we are there for. Our services are roofing, gutters, painting, and pressure washing. But 95% of the door hangers should give the message that we are a roofing contractor. We are also certified by KRV which means all of our new roof projects have a 50 year warranty which only 2% of roofing contractor can offer that. We also offer finance, and all quality work. I will like to add photos of our trucks since all of them are wrap which will build them trust.

Target Market(s)

This door hangers should be custom for Homeowners with residential Homes,,, Average customer are between 40 & 65 Years old.

Industry/Entity Type

Roofing

Contact Information for Business Card

Logo, name, phone number, credentials, and services like roofing gutters painting and pressure washing

Font styles to use
Serif
Sans Serif
Decorative

Colors
33b8a4
5c5c5c

Requirements
Must have
• I want tho have a folder design just like this business card sample i uploaded. Teal and charcoal with services ...
Nice to have
• company trucks, job photo, crew photo and credential photos
Should not have
• I dont want it too busy or crowded..

```html
<!DOCTYPE html>
<html lang="en">
<head>
<meta charset="utf-8">
<title>Tallowmere Exteriors Door Hangers</title>
<link rel="stylesheet" href="https://fonts.googleapis.com/css2?family=Roboto:wght@400;700;900&family=Oswald:wght@500&family=Exo+2:ital,wght@1,800&display=swap">
<style>
  :root {
    --teal: #0f6b66;
    --charcoal: #5c5c5c;
    --slate: #4e4f54;
    --ink: #555555;
    --white: #ffffff;
    --backdrop: #dfe9e7;
    --photo-sky: #a9bccb;
    --photo-roof: #4a4c52;
    --badge: #d9dcdc;
  }
  * { margin: 0; padding: 0; box-sizing: border-box; }
  html, body { width: 999px; height: 1200px; overflow: hidden; }
  body {
    position: relative;
    background: var(--backdrop);
    font-family: "Roboto", Arial, sans-serif;
    color: var(--ink);
  }
  .hanger {
    position: absolute;
    top: 77px;
    width: 412px;
    height: 1064px;
    background: var(--white);
    overflow: hidden;
  }
  .hanger--front { left: 76px; }
  .hanger--back { left: 526px; }
  .address-slot {
    position: absolute; left: 0; top: 0; width: 100%; height: 225px;
    background: var(--teal);
  }
  .photo {
    position: absolute;
    background: linear-gradient(180deg, var(--photo-sky) 0%, #8f9aa3 35%, var(--photo-roof) 70%, #6d6a63 100%);
  }
  .photo--inset {
    border: 4px solid var(--teal);
    background: linear-gradient(160deg, #b9b2a6 0%, #8e8a84 55%, #6b7a5e 100%);
  }

  /* Front */
  .brand {
    position: absolute; left: 0; top: 276px; width: 100%;
    display: flex; align-items: center; justify-content: center; gap: 12px;
    font-weight: 900; font-size: 27px; color: var(--charcoal);
    letter-spacing: 0.5px; text-transform: uppercase; white-space: nowrap;
  }
  .brand__mark { width: 24px; height: 24px; background: var(--teal); flex: none; }
  .tagline {
    position: absolute; left: 0; top: 357px; width: 100%; height: 52px;
    background: var(--teal); color: var(--white);
    font-family: "Oswald", "Arial Narrow", sans-serif; font-weight: 500;
    font-size: 21px; letter-spacing: 0.3px;
    display: flex; align-items: center; justify-content: center;
  }
  .services__title {
    position: absolute; left: 24px; top: 672px;
    font-size: 35px; font-weight: 700; color: var(--teal); letter-spacing: -0.3px;
  }
  .services__list {
    position: absolute; left: 30px; top: 726px; width: 370px;
    list-style: none; display: grid; grid-template-columns: 198px 1fr; row-gap: 10px;
    font-size: 17px; color: var(--ink);
  }
  .services__list li { display: flex; align-items: center; gap: 12px; }
  .services__list li::before {
    content: ""; width: 7px; height: 7px; border-radius: 50%; background: var(--teal);
  }
  .stat {
    position: absolute; left: 0; top: 796px; width: 100%;
    display: flex; justify-content: center; align-items: flex-end;
    font-weight: 900;
  }
  .stat__lead { font-size: 31px; color: var(--charcoal); margin-bottom: 12px; margin-right: 6px; }
  .stat__num { font-size: 98px; line-height: 0.85; color: var(--teal); letter-spacing: -3px; }
  .stat__unit { display: flex; flex-direction: column; align-items: center; color: var(--teal); margin-left: 2px; }
  .stat__unit span:first-child { font-size: 56px; line-height: 0.9; }
  .stat__unit span:last-child { font-size: 24px; line-height: 1; }
  .stat__note {
    position: absolute; left: 0; top: 898px; width: 100%;
    text-align: center; font-size: 15.5px; font-weight: 700; line-height: 1.35; color: var(--ink);
  }

  /* Footer */
  .footer { position: absolute; left: 0; top: 955px; width: 100%; height: 109px; }
  .footer svg { position: absolute; inset: 0; }
  .footer__text { position: absolute; top: 10px; color: var(--white); }
  .footer__label { font-family: "Exo 2", sans-serif; font-style: italic; font-weight: 800; font-size: 16px; }
  .footer__phone { font-family: "Exo 2", sans-serif; font-style: italic; font-weight: 800; font-size: 34px; line-height: 1.1; }
  .footer__web { font-size: 16px; font-weight: 700; margin-top: 4px; }

  /* Back */
  .badge {
    position: absolute; left: 100px; top: 478px; width: 212px; height: 78px;
    background: var(--badge);
  }
  .lead {
    position: absolute; left: 0; top: 573px; width: 100%;
    text-align: center; font-size: 13.5px; font-weight: 700; color: var(--ink);
  }
  .warranty {
    position: absolute; left: 0; top: 599px; width: 100%; height: 96px;
    background: var(--teal); color: var(--white);
    display: flex; align-items: center; justify-content: center; gap: 8px;
    font-weight: 900;
  }
  .warranty__num { font-size: 82px; letter-spacing: -2px; line-height: 1; }
  .warranty__word { font-size: 31px; line-height: 1.05; font-weight: 700; }
  .fine {
    position: absolute; left: 24px; width: 364px;
    font-size: 13.5px; font-weight: 700; color: var(--ink); line-height: 1.35;
  }
  .fine--one { top: 704px; text-align: center; }
  .fine--two { top: 748px; text-align: justify; }
  .contact {
    position: absolute; left: 0; top: 845px; width: 100%; text-align: center;
  }
  .contact__title { font-size: 27px; font-weight: 700; color: var(--teal); margin-bottom: 8px; }
  .contact__line { font-size: 18.5px; color: var(--ink); line-height: 1.55; }
</style>
</head>
<body>

  <section class="hanger hanger--front">
    <div class="address-slot"></div>
    <div class="brand"><span class="brand__mark"></span>Tallowmere Exteriors</div>
    <div class="tagline">PORTLAND’S TOP-RATED ROOFING COMPANY</div>
    <div class="photo" style="left:0; top:411px; width:412px; height:228px;" role="img" aria-label="Photo of a two-storey house with a freshly finished dark shingle roof"></div>
    <div class="photo photo--inset" style="left:230px; top:573px; width:158px; height:116px;" role="img" aria-label="Close-up of a roofer's gloved hands sealing a pipe flashing on shingles"></div>

    <h2 class="services__title">Our services</h2>
    <ul class="services__list">
      <li>Roofing</li><li>Painting</li>
      <li>Gutters</li><li>Pressure Washing</li>
    </ul>

    <div class="stat">
      <span class="stat__lead">Over</span>
      <span class="stat__num">20</span>
      <span class="stat__unit"><span>+</span><span>yrs</span></span>
    </div>
    <p class="stat__note">of roofing experience, using only top<br>quality materials on every home.</p>

    <div class="footer">
      <svg width="412" height="109" viewBox="0 0 412 109" aria-hidden="true">
        <polygon points="0,0 348,0 310,109 0,109" fill="var(--teal)"/>
        <polygon points="372,0 412,0 412,109 334,109" fill="var(--slate)"/>
      </svg>
      <div class="footer__text" style="left:22px;">
        <div class="footer__label">PHONE:</div>
        <div class="footer__phone">503-555-0148</div>
        <div class="footer__web">Website: tallowmereexteriors.com</div>
      </div>
    </div>
  </section>

  <section class="hanger hanger--back">
    <div class="address-slot"></div>
    <div class="photo" style="left:0; top:226px; width:412px; height:232px;" role="img" aria-label="Photo of a large stone house with a new grey slate-style roof under a blue sky"></div>
    <div class="photo photo--inset" style="left:222px; top:328px; width:158px; height:116px;" role="img" aria-label="Photo of a crew member at work beside a wrapped company truck"></div>

    <div class="badge" role="img" aria-label="KRV certified contractor badge"></div>
    <p class="lead">We are KRV certified, so every new roof carries a</p>

    <div class="warranty">
      <span class="warranty__num">50</span>
      <span class="warranty__word">year<br>warranty</span>
    </div>
    <p class="fine fine--one">Only 2% of roofing contractors can offer that.</p>
    <p class="fine fine--two">We also offer financing and quality work on every job. Look for our wrapped trucks on your street, that is our crew at work.</p>

    <div class="contact">
      <h3 class="contact__title">Contact us:</h3>
      <p class="contact__line">Portland, OR 97201, United States</p>
      <p class="contact__line">info@tallowmereexteriors.com</p>
    </div>

    <div class="footer">
      <svg width="412" height="109" viewBox="0 0 412 109" aria-hidden="true">
        <polygon points="0,0 50,0 96,109 0,109" fill="var(--slate)"/>
        <polygon points="64,0 412,0 412,109 110,109" fill="var(--teal)"/>
      </svg>
      <div class="footer__text" style="left:128px;">
        <div class="footer__label">PHONE:</div>
        <div class="footer__phone">503-555-0148</div>
        <div class="footer__web">Website: tallowmereexteriors.com</div>
      </div>
    </div>
  </section>

</body>
</html>
```